New Bicycle shop business card

Hi!
I'm looking for a business card for my new proffesional bike mechanics shop. This shop is only for fixing broken bikes and not selling bikes.
Peferbly a modern and sleek and modern design.
Colors: black, grey, red, white
Information:
Name: Rijwielwerkplaats Vanhoutte
Shop owner: Bart Vanhoutte & Marieke Segers
Website: www.rijwielwerkplaats-vanhoutte.be
Email: info@rijwielwerkplaats-vanhoutte.be
Phone number: +32471902368
Street adres: Kerkweg 46
9940 Bellebeke
Slogan/shop information: Herstellingen van alle merken.
Logo: see files.
Target Market(s)
People who seek a mechanic to fix or upgrade their bikes.
Contact Information for Business Card
Information:
Website: info@rijwielwerkplaats-vanhoutte.be
9940 Bellebeke
Logo: see files.

```html
<!DOCTYPE html>
<html lang="nl">
<head>
<meta charset="utf-8">
<title>Rijwielwerkplaats Vanhoutte – Visitekaartje</title>
<link rel="stylesheet" href="https://fonts.googleapis.com/css2?family=Lato:wght@400;700;900&display=swap">
<style>
  :root {
    --backdrop: #7a5234;
    --kraft-light: #dcbb90;
    --kraft-mid: #c99e6d;
    --kraft-dark: #b07e4f;
    --ink: #16110c;
    --card-shadow: rgba(0, 0, 0, 0.45);
  }
  * { margin: 0; padding: 0; box-sizing: border-box; }
  html, body {
    width: 1200px;
    height: 900px;
    overflow: hidden;
  }
  body {
    background: var(--backdrop);
    position: relative;
    font-family: "Lato", Arial, sans-serif;
    color: var(--ink);
  }
  .card {
    position: absolute;
    width: 556px;
    height: 343px;
    background: radial-gradient(ellipse at 30% 10%, var(--kraft-light) 0%, var(--kraft-mid) 55%, var(--kraft-dark) 100%);
    box-shadow: 3px 4px 8px var(--card-shadow);
    text-align: center;
  }
  .card--back { left: 330px; top: 90px; }
  .card--front { left: 330px; top: 470px; width: 558px; }

  .owners {
    margin-top: 83px;
    font-weight: 700;
    font-size: 20px;
    letter-spacing: 0.2px;
    text-transform: uppercase;
    line-height: 1.1;
  }
  .role { font-size: 15px; line-height: 1.2; }
  .divider {
    width: 168px;
    height: 1px;
    background: var(--ink);
    margin: 0 auto;
  }
  .role + .divider { margin-top: 12px; }
  .contact-list {
    list-style: none;
    font-size: 15px;
    line-height: 20px;
    margin: 11px 0 10px;
  }
  .address { margin-top: 14px; font-size: 15px; }

  .brand-mark {
    display: block;
    width: 56px;
    height: 56px;
    border-radius: 50%;
    background: var(--ink);
    margin: 96px auto 0;
  }
  .brand-name {
    margin: 22px auto 0;
    width: 420px;
    font-weight: 900;
    font-size: 27px;
    letter-spacing: 2px;
    line-height: 31px;
    text-transform: uppercase;
  }
  .tagline {
    margin-top: 18px;
    font-weight: 700;
    font-size: 14px;
    letter-spacing: 0.3px;
    text-transform: uppercase;
  }
</style>
</head>
<body>
  <section class="card card--back">
    <h1 class="owners">Bart Vanhoutte &amp; Marieke Segers</h1>
    <p class="role">Owner</p>
    <div class="divider"></div>
    <ul class="contact-list">
      <li>+32471902368</li>
      <li>info@rijwielwerkplaats-vanhoutte.be</li>
      <li>www.rijwielwerkplaats-vanhoutte.be</li>
    </ul>
    <div class="divider"></div>
    <p class="address">Kerkweg 46 9940 Bellebeke</p>
  </section>

  <section class="card card--front">
    <span class="brand-mark"></span>
    <h2 class="brand-name">Rijwielwerkplaats Vanhoutte</h2>
    <p class="tagline">Herstellingen van alle merken</p>
  </section>
</body>
</html>
```